Water ATM Card

Need a design for water ATM cards. Size of card is 3.375 x 2.125 inch
On the Front include the Cedar hollow Logo.
Bottom right corner should have Price $100
On the Back
This card is to be used to access water refills at any Cedar Hollow Water Vending Machines.
Please contact (869) 418 2930 or (869) 534 1276 or email clearflowbox@mailvista.example for any assistance or recharging of card.

```html
<!DOCTYPE html>
<html lang="en">
<head>
<meta charset="utf-8">
<title>Cedar Hollow Water Card</title>
<link href="https://fonts.googleapis.com/css2?family=Montserrat:wght@400;500;700&display=swap" rel="stylesheet">
<style>
  :root {
    --backdrop: #9a9a9a;
    --card-white: #ffffff;
    --card-shade: #eeeeee;
    --navy-top: #2f6499;
    --navy-bottom: #2b3678;
    --brand-blue: #1f5fae;
    --name-blue: #1c3f94;
    --ink: #222222;
    --price-green: #1e9a3a;
    --rule-blue: #2a63b5;
  }
  * { box-sizing: border-box; margin: 0; padding: 0; }
  html, body { width: 1200px; height: 900px; overflow: hidden; }
  body {
    background: var(--backdrop);
    font-family: "Montserrat", sans-serif;
    position: relative;
  }
  .card {
    position: absolute;
    width: 620px;
    height: 390px;
    border-radius: 4px;
    box-shadow: 0 10px 24px rgba(0,0,0,0.25);
    overflow: hidden;
  }
  .card-back {
    left: 70px; top: 50px;
    background: linear-gradient(160deg, var(--navy-top), var(--navy-bottom));
    color: #fff;
  }
  .card-front {
    left: 510px; top: 460px;
    background: linear-gradient(160deg, var(--card-white) 40%, var(--card-shade));
  }
  .brand {
    position: absolute;
    display: flex;
    align-items: center;
    gap: 16px;
    font-weight: 700;
    letter-spacing: 1px;
    text-transform: uppercase;
    white-space: nowrap;
  }
  .brand-dot { width: 34px; height: 34px; border-radius: 50%; }
  .card-back .brand { left: 50%; top: 140px; transform: translateX(-50%); font-size: 46px; color: #fff; }
  .card-back .brand-dot { background: #fff; }
  .assist-note {
    position: absolute; left: 0; right: 0; top: 290px;
    text-align: center; font-size: 15px; font-weight: 400;
  }
  .card-front .brand { left: 40px; top: 90px; font-size: 46px; color: var(--brand-blue); }
  .card-front .brand-dot { background: var(--brand-blue); }
  .holder {
    position: absolute; right: 350px; top: 230px; text-align: right;
  }
  .holder-name { font-size: 22px; font-weight: 700; color: var(--name-blue); text-transform: uppercase; }
  .holder-role { font-size: 14px; color: var(--ink); margin-top: 4px; }
  .contacts {
    position: absolute; left: 290px; top: 200px;
    border-left: 2px solid var(--rule-blue);
    padding-left: 14px;
    list-style: none;
    font-size: 14px; color: var(--ink);
  }
  .contacts li { display: flex; align-items: center; gap: 8px; height: 24px; }
  .contacts svg { width: 14px; height: 14px; fill: var(--rule-blue); flex: none; }
  .price {
    position: absolute; right: 40px; bottom: 36px;
    font-size: 24px; font-weight: 700; color: var(--price-green);
  }
</style>
</head>
<body>
  <section class="card card-back" aria-label="Card back">
    <div class="brand"><span class="brand-dot"></span>Cedar Hollow</div>
    <p class="assist-note">for any assistance or recharging of card.</p>
  </section>

  <section class="card card-front" aria-label="Card front">
    <div class="brand"><span class="brand-dot"></span>Cedar Hollow</div>
    <div class="holder">
      <p class="holder-name">Daniel Reyes</p>
      <p class="holder-role">OWER</p>
    </div>
    <ul class="contacts">
      <li><svg viewBox="0 0 24 24"><path d="M6.6 10.8a15.1 15.1 0 0 0 6.6 6.6l2.2-2.2a1 1 0 0 1 1-.25 11.4 11.4 0 0 0 3.6.6 1 1 0 0 1 1 1V20a1 1 0 0 1-1 1A17 17 0 0 1 3 4a1 1 0 0 1 1-1h3.5a1 1 0 0 1 1 1c0 1.25.2 2.45.6 3.6a1 1 0 0 1-.25 1z"/></svg>(869) 418 2930</li>
      <li><svg viewBox="0 0 24 24"><path d="M7 1h10a2 2 0 0 1 2 2v18a2 2 0 0 1-2 2H7a2 2 0 0 1-2-2V3a2 2 0 0 1 2-2zm0 3v14h10V4zm5 15.5a1.2 1.2 0 1 0 0 2.4 1.2 1.2 0 0 0 0-2.4z"/></svg>(869) 534 1276</li>
      <li><svg viewBox="0 0 24 24"><path d="M2 5h20v14H2zm2 2v.5l8 5 8-5V7l-8 5z"/></svg>clearflowbox@mailvista.example</li>
      <li><svg viewBox="0 0 24 24"><path d="M12 2a10 10 0 1 0 0 20 10 10 0 0 0 0-20zm6.9 9h-3a15 15 0 0 0-1.4-6A8 8 0 0 1 18.9 11zM12 4c.9 1.2 1.8 3.6 2 7h-4c.2-3.4 1.1-5.8 2-7zM9.5 5a15 15 0 0 0-1.4 6h-3A8 8 0 0 1 9.5 5zm-4.4 8h3a15 15 0 0 0 1.4 6A8 8 0 0 1 5.1 13zm6.9 7c-.9-1.2-1.8-3.6-2-7h4c-.2 3.4-1.1 5.8-2 7zm2.5-1a15 15 0 0 0 1.4-6h3a8 8 0 0 1-4.4 6z"/></svg>www.cedarhollowwater.example</li>
    </ul>
    <p class="price">Price $100</p>
  </section>
</body>
</html>
```